Flyer for Tallow Brisko - Design Agency

We need a 4-page square flyer measuring 14.8x14.8cm per page, to fold out, for a design agency targeting small businesses.
The design should be very modern. There shouldn't be too much content visible.
The background should be black. The color of the logo (attached) can also be used. The content is also attached and divided per page. We are open to alternative suggestions regarding the division.

```html
<!DOCTYPE html>
<html lang="de">
<head>
<meta charset="utf-8">
<title>Tallow Brisko – Faltflyer</title>
<link href="https://fonts.googleapis.com/css2?family=Poppins:wght@300;400;500;600;700;800&display=swap" rel="stylesheet">
<style>
  :root{
    --stage:#dcdcde;
    --page:#1d1d1d;
    --page-deep:#141414;
    --teal:#5ed6d3;
    --teal-light:#a9f1ec;
    --white:#f4f4f4;
    --muted:#cfcfcf;
    --line:#bdbdbd;
  }
  *{box-sizing:border-box;margin:0;padding:0}
  html,body{width:1200px;height:1185px;overflow:hidden;background:var(--stage);font-family:'Poppins',sans-serif;color:var(--white)}
  .spread{position:absolute;left:60px;width:1080px;height:540px;display:flex;box-shadow:0 12px 30px rgba(0,0,0,.18)}
  .spread--outer{top:35px}
  .spread--inner{top:610px}
  .page{position:relative;width:540px;height:540px;background:var(--page);overflow:hidden}
  .page--left{background:linear-gradient(90deg,var(--page) 70%,var(--page-deep))}
  .page--right{background:linear-gradient(90deg,var(--page-deep),var(--page) 30%)}

  .decor{position:absolute;background:linear-gradient(135deg,var(--teal),var(--teal-light));opacity:.85}
  .decor--back{left:0;top:380px;width:210px;height:160px;border-radius:0 6px 0 0}
  .decor--front-top{left:100px;top:0;width:120px;height:170px;border-radius:0 0 6px 6px}
  .decor--front-side{left:240px;top:245px;width:300px;height:50px;border-radius:6px 0 0 6px}

  .brand-circle{position:absolute;border-radius:50%;background:var(--page-deep);border:4px solid var(--white);display:flex;align-items:center;justify-content:center;text-align:center}
  .brand-name{font-weight:600;color:var(--teal);font-size:22px;line-height:1.1}
  .tagline{position:absolute;text-transform:uppercase;line-height:1.2;white-space:nowrap}
  .tagline .light{display:block;font-weight:400}
  .tagline .bold{display:block;font-weight:800}

  /* back cover */
  .contact-pill{position:absolute;left:40px;top:60px;width:410px;height:34px;border:1.5px solid var(--white);border-radius:17px;font-size:14px;font-weight:600;padding-left:44px;line-height:31px}
  .contact-pill .badge{position:absolute;left:-6px;top:-3px;width:36px;height:38px;background:var(--teal);border-radius:6px 6px 6px 0;display:flex;align-items:center;justify-content:center}
  .contact-list{position:absolute;left:50px;top:150px;list-style:none}
  .contact-list li{display:flex;align-items:flex-start;gap:14px;font-size:15px;font-weight:600;margin-bottom:12px;line-height:1.3}
  .contact-icon{flex:none;width:26px;height:26px;border-radius:50%;background:var(--teal);display:flex;align-items:center;justify-content:center}

  /* photos & illustrations */
  .photo{position:absolute;border-radius:6px}
  .photo--portrait{left:260px;top:20px;width:200px;height:200px;background:linear-gradient(180deg,#6b6b6b,#9a9a9a 60%,#3a3a3a)}
  .photo--collage{left:330px;top:30px;width:180px;height:150px;background:linear-gradient(135deg,#cfe4ee,#e8eef2 60%,#b9d6e4)}
  .illustration--bulb{position:absolute;left:50px;top:320px;width:180px;height:190px;border-radius:6px;background:linear-gradient(180deg,#2a6f74,#3a3a3a)}

  /* inner left */
  .intro-pill{position:absolute;left:40px;top:150px;width:220px;background:var(--teal);color:var(--page-deep);border-radius:20px 20px 20px 0;padding:6px 16px;font-size:15px;line-height:1.2}
  .intro-pill strong{display:block;font-weight:700}
  .intro-box{position:absolute;left:60px;top:200px;width:210px;border:1.5px solid var(--line);border-radius:6px;padding:14px 14px 10px;font-size:12px;line-height:1.35;color:var(--muted)}
  .statement{position:absolute;left:270px;top:260px;width:270px;height:280px;border-radius:40px 0 0 0;background:linear-gradient(135deg,var(--teal),var(--teal-light));color:var(--page-deep);padding:50px 30px 0 40px;font-size:17px;line-height:1.35}

  /* inner right */
  .section-pill{position:absolute;background:var(--teal);color:var(--page-deep);font-weight:700;font-size:15px;padding:4px 22px 4px 14px;border-radius:16px 16px 16px 0}
  .service{position:absolute;width:220px;border:1.5px solid var(--line);border-radius:6px;padding:10px 12px 10px 44px}
  .service h3{font-size:13px;font-weight:700;margin-bottom:4px}
  .service p{font-size:10.5px;line-height:1.35;color:var(--muted)}
  .service .icon{position:absolute;left:10px;top:10px;width:24px;height:24px;background:var(--teal);border-radius:5px 5px 5px 0;display:flex;align-items:center;justify-content:center}
  .reason{position:absolute;top:355px;width:150px;height:130px;border-top:1.5px solid var(--line);border-right:1.5px solid var(--line);border-radius:0 6px 0 0;padding:8px 12px 0 26px}
  .reason::after{content:"";position:absolute;right:-5px;bottom:-5px;width:8px;height:8px;border-radius:50%;background:var(--teal)}
  .reason h3{font-size:13px;font-weight:700;line-height:1.2;margin-bottom:8px}
  .reason p{font-size:10.5px;line-height:1.35;color:var(--muted)}
  .reason .icon{position:absolute;left:-2px;top:22px;width:22px;height:22px;border-radius:50%;background:var(--white);display:flex;align-items:center;justify-content:center}
</style>
</head>
<body>

<section class="spread spread--outer">
  <article class="page page--left back-cover">
    <div class="decor decor--back" role="img" aria-label="Dekorative türkise Schwungbänder"></div>
    <div class="contact-pill">
      <span class="badge"><svg width="18" height="18" viewBox="0 0 18 18"><circle cx="9" cy="6" r="4" fill="var(--page-deep)"/><path d="M2 17c1-5 13-5 14 0Z" fill="var(--page-deep)"/></svg></span>
      Kontaktiere uns für eine kostenlose Beratung!
    </div>
    <ul class="contact-list">
      <li><span class="contact-icon"><svg width="14" height="14" viewBox="0 0 14 14"><path d="M3 1l2 3-1 2c1 2 2 3 4 4l2-1 3 2-1 2C6 13 1 8 1 2Z" fill="var(--page-deep)"/></svg></span>+49 000 11223</li>
      <li><span class="contact-icon"><svg width="14" height="12" viewBox="0 0 14 12"><rect x="1" y="2" width="12" height="9" rx="1" fill="var(--page-deep)"/><path d="M1 3l6 4 6-4" stroke="var(--teal)" fill="none"/></svg></span>hallo@tallowbrisko.de</li>
      <li><span class="contact-icon"><svg width="12" height="14" viewBox="0 0 12 14"><path d="M6 13C2 8 1 6 1 5a5 5 0 0 1 10 0c0 1-1 3-5 8Z" fill="var(--page-deep)"/><circle cx="6" cy="5" r="2" fill="var(--teal)"/></svg></span>Kastanienallee 12<br>60594 Frankfurt</li>
    </ul>
    <div class="brand-circle" style="left:335px;top:190px;width:175px;height:175px;">
      <span class="brand-name">Tallow<br>Brisko</span>
    </div>
    <p class="tagline" style="left:235px;top:400px;font-size:24px;">
      <span class="light">Designs, die wirken.</span>
      <span class="bold">Marken, die bleiben.</span>
    </p>
  </article>

  <article class="page page--right front-cover">
    <div class="decor decor--front-top" role="img" aria-label="Dekorative türkise Schwungbänder"></div>
    <div class="decor decor--front-side" role="img" aria-label="Dekorative türkise Schwungbänder"></div>
    <div class="photo photo--portrait" role="img" aria-label="Schwarzweißfoto einer lächelnden Frau mit Glühbirne als Ideensymbol"></div>
    <div class="brand-circle" style="left:40px;top:190px;width:175px;height:175px;">
      <span class="brand-name">Tallow<br>Brisko</span>
    </div>
    <p class="tagline" style="left:70px;top:400px;font-size:22px;">
      <span class="light">Dein Unternehmen.</span>
      <span class="bold">Dein Stil. Unser Design.</span>
    </p>
  </article>
</section>

<section class="spread spread--inner">
  <article class="page page--left intro">
    <div class="photo photo--collage" role="img" aria-label="Collage einer Frau mit Laptop, Diagramm und Rakete"></div>
    <div class="intro-pill">Modern, mutig, markant<strong>Tallow Brisko</strong></div>
    <div class="intro-box">Gestaltet die Zukunft deines Unternehmensauftritts.</div>
    <div class="illustration--bulb" role="img" aria-label="Illustration einer Hand, die eine leuchtende Glühbirne hält"></div>
    <div class="statement">Wir machen aus Ideen visuelle Erlebnisse und sorgen dafür, dass deine Marke im Gedächtnis bleibt.<br>+ Grafiken</div>
  </article>

  <article class="page page--right services">
    <span class="section-pill" style="left:24px;top:40px;">Unsere Leistungen</span>
    <div class="service" style="left:30px;top:85px;">
      <span class="icon"><svg width="14" height="14" viewBox="0 0 14 14"><path d="M2 12l3-6 6-5-1 6-6 3Z" fill="var(--page-deep)"/></svg></span>
      <h3>Unsere Leistungen</h3>
      <p>Nicht nur Papier, sondern deine Botschaft im perfekten Look.</p>
    </div>
    <div class="service" style="left:290px;top:40px;">
      <span class="icon"><svg width="14" height="14" viewBox="0 0 14 14"><rect x="2" y="5" width="4" height="8" fill="var(--page-deep)"/><rect x="7" y="2" width="5" height="11" fill="var(--page-deep)"/></svg></span>
      <h3>Corporate Identity</h3>
      <p>Ein Design, das deine Marke spricht – individuell, stark, unvergesslich.</p>
    </div>
    <div class="service" style="left:30px;top:200px;">
      <span class="icon"><svg width="14" height="14" viewBox="0 0 14 14"><rect x="1" y="5" width="12" height="6" rx="1" fill="var(--page-deep)"/><rect x="4" y="2" width="6" height="3" fill="var(--page-deep)"/></svg></span>
      <h3>Digital &amp; Druck</h3>
      <p>Ob Social Media Grafiken oder klassisches Printdesign – wir sind da, wo du uns brauchst.</p>
    </div>
    <div class="service" style="left:290px;top:150px;">
      <span class="icon"><svg width="14" height="14" viewBox="0 0 14 14"><circle cx="7" cy="7" r="5" fill="var(--page-deep)"/></svg></span>
      <h3>Alles aus einer Hand</h3>
      <p>Logo, Farben, Typografie, Flyer und vieles mehr – wir bauen das Fundament für deinen Erfolg.</p>
    </div>

    <span class="section-pill" style="left:24px;top:315px;">Warum wir?</span>
    <div class="reason" style="left:40px;">
      <span class="icon"><svg width="12" height="12" viewBox="0 0 12 12"><path d="M2 6l3 3 5-6" stroke="var(--page-deep)" stroke-width="2" fill="none"/></svg></span>
      <h3>Dein Style, unser Know-how</h3>
      <p>Wir kombinieren deine Vision mit moderner Ästhetik.</p>
    </div>
    <div class="reason" style="left:205px;">
      <span class="icon"><svg width="12" height="12" viewBox="0 0 12 12"><circle cx="6" cy="4" r="3" fill="var(--page-deep)"/><path d="M1 12c1-4 9-4 10 0Z" fill="var(--page-deep)"/></svg></span>
      <h3>Persönlicher Service</h3>
      <p>Wir hören zu und setzen um, was dich einzigartig macht.</p>
    </div>
    <div class="reason" style="left:370px;">
      <span class="icon"><svg width="12" height="12" viewBox="0 0 12 12"><path d="M6 1l1.5 3.5L11 5l-2.5 2.5L9 11 6 9 3 11l.5-3.5L1 5l3.5-.5Z" fill="var(--page-deep)"/></svg></span>
      <h3>Flexible Lösungen</h3>
      <p>für die unterschiedlichsten Anforderungen</p>
    </div>
  </article>
</section>

</body>
</html>
```